Postcard design to acquire new clients for my Property Management Company

I'm looking for a postcard design that I can send to prospective clients detailing information about my company and services.
Postcard should be eye catching and contain information from www.bramblecrestpm.com. I've provided a few screen shots for the most important information and my logo.
Target Market(s)
Real Estate
Industry/Entity Type
Real Estate
Font styles to use
Sans Serif
Requirements
Must have
- Must be eye catching!! this will be a direct mail piece - I'd like for the card to be read and not tossed in the trash immediately.
Design que from the logo.
A place to write / print the receipts name and address.
our physical address - 2387 Hollow Pine Road, Lubbock, TX 79852.
Should not have
- the contact information on the business card is not accurate - please use info from website.

```html
<!DOCTYPE html>
<html lang="en">
<head>
<meta charset="utf-8">
<title>Bramblecrest Property Management Postcard</title>
<link href="https://fonts.googleapis.com/css2?family=Roboto:wght@300;400;500;700;900&display=swap" rel="stylesheet">
<style>
:root{
  --navy:#1f4f8b;
  --navy-dark:#1a4275;
  --ink:#333a44;
  --grey:#8a8d92;
  --paper:#ffffff;
  --bg:#eef0f3;
  --rule:#444;
}
*{box-sizing:border-box;margin:0;padding:0}
html,body{width:1200px;height:1199px;overflow:hidden;background:var(--bg);font-family:"Roboto",Arial,sans-serif;color:var(--ink)}
.card{position:absolute;left:190px;width:820px;height:560px;background:var(--paper);box-shadow:4px 6px 14px rgba(0,0,0,.25);overflow:hidden}
.card--front{top:30px}
.card--back{top:609px}
.deco{position:absolute;inset:0}
.hero-art{position:absolute;left:8px;top:35px;width:345px;height:270px;border-radius:12px;background:radial-gradient(circle at 50% 45%,#9eaabb 0%,#5e6f88 45%,#3d9a56 75%,rgba(255,255,255,0) 76%)}
.brand{position:absolute;left:372px;top:28px;color:var(--navy)}
.brand__name{font-size:33px;font-weight:700;letter-spacing:5px;line-height:1}
.brand__tag{font-size:15px;font-weight:400;letter-spacing:3.4px;margin-top:2px}
.headline{position:absolute;left:372px;top:124px;width:440px;font-size:27px;font-weight:900;line-height:1.18;color:var(--navy)}
.lede{position:absolute;left:372px;top:195px;font-size:14px}
.plan{position:absolute;font-size:12px;line-height:1.3}
.plan__name{font-size:19px;font-weight:400;color:var(--ink)}
.plan__note{font-size:12px}
.plan__rate{font-size:25px;font-weight:700;color:var(--navy);margin-top:6px;line-height:1}
.plan__unit{font-size:12px;margin-bottom:12px}
.plan__list{font-size:11.5px;line-height:1.33}
.plan--lease{left:372px;top:220px}
.plan--full{left:145px;top:385px}
.plan--premium{left:538px;top:385px}
.divider{position:absolute;left:500px;top:395px;width:1px;height:140px;background:#9aa8bd}
.services{position:absolute;left:0;top:0;width:415px;height:560px;background:var(--navy);color:#fff;overflow:hidden}
.services__title{position:absolute;top:32px;width:100%;text-align:center;font-size:27px;font-weight:700}
.services__sub{position:absolute;top:68px;width:100%;text-align:center;font-size:14px;font-weight:300}
.service{position:absolute;display:flex;align-items:center;gap:10px;font-size:21px;font-weight:400}
.service svg{width:36px;height:36px;flex:none}
.contact{position:absolute;left:16px;top:514px;font-size:19px}
.contact b{font-weight:700}
.stamp{position:absolute;left:688px;top:38px;width:100px;height:100px;border:1.5px solid var(--rule)}
.address-line{position:absolute;left:437px;width:368px;height:1px;background:var(--rule)}
</style>
</head>
<body>

<section class="card card--front">
  <svg class="deco" viewBox="0 0 820 560" aria-hidden="true">
    <polygon points="0,245 0,560 118,560" fill="#1f4f8b"/>
    <polygon points="0,330 0,560 50,560" fill="#fff"/>
    <polygon points="40,560 70,392 140,560" fill="#1f4f8b"/>
    <polygon points="60,560 75,500 95,560" fill="#fff"/>
    <polygon points="820,245 820,560 730,560" fill="#1f4f8b"/>
    <polygon points="820,350 820,560 790,560" fill="#fff"/>
    <polygon points="705,560 748,392 790,560" fill="#1f4f8b"/>
    <polygon points="740,560 752,515 765,560" fill="#fff"/>
  </svg>
  <div class="hero-art" role="img" aria-label="Illustration of a house under a magnifying glass with a key and a gold dollar sign"></div>
  <div class="brand">
    <div class="brand__name">BRAMBLECREST</div>
    <div class="brand__tag">PROPERTY MANAGEMENT</div>
  </div>
  <h1 class="headline">CHOOSE THE RIGHT PROPERTY MANAGEMENT SYSTEM</h1>
  <p class="lede">Selecting the wrong manager could be your costliest mistake ever.</p>

  <div class="plan plan--lease" style="top:222px">
    <div class="plan__name" style="margin-top:16px">Lease Only</div>
    <div class="plan__note">You Just Need Tenants</div>
    <div class="plan__rate">9%</div>
    <div class="plan__unit">of annual lease</div>
    <div class="plan__list">Professional Photography | Marketing &amp; Advertising<br>Property Showings | Tenant Screening &amp; Qualifications<br>Lease Execution | Move In Coordination</div>
  </div>

  <div class="plan plan--full">
    <div class="plan__name">Full Service</div>
    <div class="plan__note">Our Most Popular</div>
    <div class="plan__rate">10%</div>
    <div class="plan__unit">of monthly rent</div>
    <div class="plan__list">Includes Leasing Service | 24/7 Emergency Response<br>Move In &amp; Out Inspections | Professional Lease Enforcement<br>Schedule &amp; Oversee all Repairs | Pay all Invoices<br>Monthly &amp; Year End Statements | Annual Market Rent Analysis</div>
  </div>

  <div class="divider"></div>

  <div class="plan plan--premium">
    <div class="plan__name">Premium Service</div>
    <div class="plan__note">Our Premier Service</div>
    <div class="plan__rate">12%</div>
    <div class="plan__unit">of monthly rent</div>
    <div class="plan__list">Includes Full Service Features<br>Professional Video Marketing<br>Home Warranty Coordination<br>Tenant Retention Program</div>
  </div>
</section>

<section class="card card--back">
  <div class="services">
    <svg class="deco" viewBox="0 0 415 560" aria-hidden="true">
      <polygon points="30,560 150,120 300,560" fill="#fff" opacity=".07"/>
      <polygon points="120,560 170,380 230,560" fill="#1f4f8b"/>
    </svg>
    <h2 class="services__title">Discover Our Services</h2>
    <p class="services__sub">We offer full-service property management solutions</p>

    <div class="service" style="left:32px;top:94px">
      <svg viewBox="0 0 36 36"><circle cx="18" cy="18" r="16" fill="none" stroke="#fff" stroke-width="2"/><path d="M9 19 L18 11 L27 19 M12 17 V26 H24 V17" fill="none" stroke="#fff" stroke-width="2.4" stroke-linejoin="round"/></svg>Property Marketing</div>
    <div class="service" style="left:148px;top:145px">
      <svg viewBox="0 0 36 36"><circle cx="18" cy="18" r="16" fill="none" stroke="#fff" stroke-width="2"/><circle cx="14" cy="14" r="3.4" fill="#fff"/><circle cx="22" cy="14" r="3.4" fill="#fff"/><path d="M8 25 q6-8 12 0 M16 25 q6-8 12 0" fill="#fff"/></svg>Tenant Screening</div>
    <div class="service" style="left:32px;top:196px">
      <svg viewBox="0 0 36 36"><circle cx="18" cy="18" r="16" fill="none" stroke="#fff" stroke-width="2"/><text x="18" y="25" text-anchor="middle" font-size="19" font-weight="700" fill="#fff" font-family="Roboto,sans-serif">$</text></svg><span style="margin-left:12px">Rent Collection</span></div>
    <div class="service" style="left:148px;top:242px">
      <svg viewBox="0 0 36 36"><circle cx="18" cy="18" r="16" fill="none" stroke="#fff" stroke-width="2"/><path d="M12 25 L20 16 M17 11 L24 18 L26 15 L20 9 Z" fill="#fff" stroke="#fff" stroke-width="2.4" stroke-linejoin="round"/></svg><span style="margin-left:12px">Maintenance</span></div>
    <div class="service" style="left:32px;top:288px">
      <svg viewBox="0 0 36 36"><circle cx="18" cy="18" r="16" fill="none" stroke="#fff" stroke-width="2"/><circle cx="16" cy="16" r="5.5" fill="none" stroke="#fff" stroke-width="2.4"/><path d="M20 20 L26 26" stroke="#fff" stroke-width="3"/></svg><span style="margin-left:12px">Property Inspections</span></div>
    <div class="service" style="left:148px;top:339px">
      <svg viewBox="0 0 36 36"><circle cx="18" cy="18" r="16" fill="none" stroke="#fff" stroke-width="2"/><path d="M11 25 H25 M13 23 V17 M16 23 V14 M19 23 V16 M22 23 V12" stroke="#fff" stroke-width="1.8"/></svg><span style="margin-left:12px">Financial Reporting</span></div>
    <div class="service" style="left:32px;top:390px">
      <svg viewBox="0 0 36 36"><circle cx="18" cy="18" r="16" fill="none" stroke="#fff" stroke-width="2"/><path d="M18 9 L26 12 V18 Q26 24 18 28 Q10 24 10 18 V12 Z" fill="none" stroke="#fff" stroke-width="2.2"/><path d="M18 12 V25 Q23 22 23 18 V14 Z" fill="#fff"/></svg><span style="margin-left:12px">Evictions</span></div>
    <div class="service" style="left:148px;top:437px">
      <svg viewBox="0 0 36 36"><circle cx="18" cy="18" r="16" fill="none" stroke="#fff" stroke-width="2"/><path d="M18 10 V26 M12 26 H24 M10 13 H26 M10 13 L7 20 H13 Z M26 13 L23 20 H29 Z" fill="none" stroke="#fff" stroke-width="1.8" stroke-linejoin="round"/></svg><span style="margin-left:12px">Legal Guidance</span></div>

    <p class="contact"><b>(555) 214-7390</b> | info@bramblecrestpm.com</p>
  </div>
  <div class="stamp"></div>
  <div class="address-line" style="top:305px"></div>
  <div class="address-line" style="top:368px"></div>
  <div class="address-line" style="top:430px"></div>
  <div class="address-line" style="top:494px"></div>
</section>

</body>
</html>
```